BOLD & MINIMALIST DESIGN NEEDED

We want a very bold but minimalistic business card design that is impactful and utilizes both sides of the business card. Our current logo is included for your use.

We want bold fonts and good use of negative space. We don't want the logo to overpower the design.

Target Market(s)

Professionals who are building new commercial buildings.

Industry/Entity Type

Construction

Contact Information for Business Card

Name, Title, email, office phone, cell phone, website

Font styles to use
Serif
Sans Serif

Requirements
Must have
• Bold design!

```html
<!DOCTYPE html>
<html lang="en">
<head>
<meta charset="UTF-8">
<title>Ridgeline Business Card</title>
<link href="https://fonts.googleapis.com/css2?family=Poppins:wght@400;600;700&display=swap" rel="stylesheet">
<style>
  :root {
    --backdrop: #232323;
    --card: #262627;
    --card-edge: #2e2e2f;
    --accent: #7dba2c;
    --text-light: #e6e6e6;
    --text-soft: #c9c9c9;
    --mark-grey: #3d3d3f;
  }
  * { margin: 0; padding: 0; box-sizing: border-box; }
  html, body {
    width: 1200px; height: 576px; overflow: hidden;
    background: var(--backdrop);
    font-family: "Poppins", sans-serif;
  }
  .canvas { position: relative; width: 1200px; height: 576px; }
  .card {
    position: absolute;
    top: 139px;
    background: linear-gradient(160deg, var(--card-edge), var(--card) 60%);
    border-radius: 8px;
    box-shadow: 0 3px 8px rgba(0,0,0,0.45);
  }
  .card-front { left: 102px; width: 484px; height: 293px; }
  .card-back { left: 597px; width: 479px; height: 291px; }

  .front-name {
    position: absolute; left: 0; right: 0; top: 100px;
    text-align: center;
    font-weight: 700; font-size: 52px; letter-spacing: 0.04em;
    color: var(--mark-grey);
  }
  .front-url {
    position: absolute; left: 0; right: 0; top: 251px;
    text-align: center;
    font-size: 13px; letter-spacing: 0.62em;
    color: var(--text-soft);
  }

  .person-name {
    position: absolute; left: 30px; top: 30px;
    font-weight: 600; font-size: 21px; color: var(--accent);
  }
  .person-title {
    position: absolute; left: 30px; top: 57px;
    font-size: 12px; color: var(--text-light);
  }
  .contact-list {
    position: absolute; left: 32px; top: 213px;
    list-style: none;
  }
  .contact-list li {
    display: flex; align-items: center; gap: 8px;
    font-size: 12.5px; line-height: 17px; color: var(--text-light);
  }
  .contact-list svg { width: 10px; height: 10px; fill: var(--accent); }

  .brand {
    position: absolute; right: 32px; top: 238px;
    display: flex; align-items: center; gap: 8px;
  }
  .brand-square { width: 14px; height: 14px; background: var(--accent); }
  .brand-name {
    font-weight: 700; font-size: 24px; letter-spacing: 0.02em;
    color: var(--text-light);
  }
</style>
</head>
<body>
<div class="canvas">
  <section class="card card-front">
    <div class="front-name">RIDGELINE</div>
    <div class="front-url">www.ridgeline.com</div>
  </section>

  <section class="card card-back">
    <div class="person-name">Tomas Rivera</div>
    <div class="person-title">Director</div>
    <ul class="contact-list">
      <li>
        <svg viewBox="0 0 10 10"><path d="M1 4 Q5 0 9 4 L8 5 L6.5 4 L6.5 3 Q5 2.6 3.5 3 L3.5 4 L2 5 Z M2.5 6 L7.5 6 L8 9 L2 9 Z"/></svg>
        555-014-0127
      </li>
      <li>
        <svg viewBox="0 0 10 10"><path d="M0 2 H10 V8 H0 Z" /><path d="M0 2 L5 6 L10 2" fill="none" stroke="#262627" stroke-width="1"/></svg>
        tomas@ridgeline.com
      </li>
      <li>
        <svg viewBox="0 0 10 10"><circle cx="5" cy="5" r="4.5"/><path d="M0.5 5 H9.5 M5 0.5 V9.5" stroke="#262627" stroke-width="0.8"/></svg>
        www.ridgeline.com
      </li>
    </ul>
    <div class="brand">
      <span class="brand-square"></span>
      <span class="brand-name">RIDGELINE</span>
    </div>
  </section>
</div>
</body>
</html>
```